Mosquito and outdoor pest management

The uploaded logo must be integrated as the main theme of the card. I would like it to be modern and eye catching. Maybe some backround images or light silver metallic background.
Space enough at the base for contact info to be put in- phone numbers,emails,names,website.
Space on the back for short blog and lines for hand writing..calling card.
Commercial- golf courses, schools, outdoor function properties, pre event treatments.
Residential- retirement villages, townhome complexes and general houses
Management

```html
<!DOCTYPE html>
<html lang="en">
<head>
<meta charset="utf-8">
<title>Bayline Mosquito – Business Card</title>
<link rel="stylesheet" href="https://fonts.googleapis.com/css2?family=Source+Sans+3:wght@400;600&display=swap">
<style>
  :root {
    --backdrop: #444444;
    --silver-light: #ffffff;
    --silver-mid: #e6e6e6;
    --silver-dark: #bdbdbd;
    --accent-red: #e8202a;
    --ink-black: #111111;
    --ink-grey: #555555;
    --rule-grey: #6a6a6a;
  }
  * { box-sizing: border-box; margin: 0; padding: 0; }
  html, body {
    width: 1105px;
    height: 1200px;
    overflow: hidden;
  }
  body {
    background: var(--backdrop);
    font-family: "Source Sans 3", "Myriad Pro", Arial, sans-serif;
    position: relative;
  }
  .card {
    position: absolute;
    left: 196px;
    width: 720px;
    height: 411px;
    overflow: hidden;
    background: radial-gradient(ellipse 65% 75% at 50% 45%, var(--silver-light) 0%, var(--silver-mid) 45%, var(--silver-dark) 100%);
  }
  .card--front { top: 146px; }
  .card--back { top: 602px; }

  .corner-swoosh {
    position: absolute;
    width: 175px;
    height: 175px;
  }
  .corner-swoosh--top-left { left: 0; top: 0; }
  .corner-swoosh--bottom-right { right: 0; bottom: 0; transform: rotate(180deg); }

  .brand-name {
    position: absolute;
    color: var(--ink-black);
    font-weight: 600;
    white-space: nowrap;
    display: flex;
    align-items: center;
    gap: 10px;
  }
  .brand-name__dot {
    display: inline-block;
    border-radius: 50%;
    background: var(--accent-red);
  }
  .card--front .brand-name {
    right: 34px;
    top: 42px;
    font-size: 34px;
  }
  .card--front .brand-name__dot { width: 16px; height: 16px; }

  .contact {
    position: absolute;
    left: 30px;
    top: 220px;
  }
  .contact__name {
    color: var(--accent-red);
    font-size: 26px;
    font-weight: 600;
    line-height: 1.1;
  }
  .contact__role {
    color: var(--ink-black);
    font-size: 20px;
    line-height: 1.3;
    margin-bottom: 12px;
  }
  .contact__list { list-style: none; }
  .contact__item {
    display: flex;
    align-items: center;
    gap: 10px;
    color: var(--ink-grey);
    font-size: 19px;
    line-height: 27.5px;
  }
  .contact__icon { width: 16px; height: 16px; flex: none; margin-left: 6px; }

  .note-lines {
    position: absolute;
    left: 25px;
    right: 33px;
    top: 0;
  }
  .note-lines__rule {
    position: absolute;
    left: 0;
    right: 0;
    border-top: 1.5px dotted var(--rule-grey);
  }

  .card--back .brand-name {
    left: 0;
    right: 0;
    justify-content: center;
    top: 315px;
    font-size: 50px;
  }
  .card--back .brand-name__dot { width: 22px; height: 22px; }
</style>
</head>
<body>

<section class="card card--front" aria-label="Business card front">
  <svg class="corner-swoosh corner-swoosh--top-left" viewBox="0 0 175 175" aria-hidden="true">
    <path d="M0 0 H162 C85 12 18 75 0 162 Z" fill="var(--accent-red)"/>
    <path d="M160 2 C80 18 16 82 3 165" fill="none" stroke="var(--ink-black)" stroke-width="5" stroke-linecap="round"/>
  </svg>

  <div class="brand-name"><span class="brand-name__dot"></span>Bayline Mosquito</div>

  <div class="contact">
    <p class="contact__name">Alex Carter</p>
    <p class="contact__role">CEO/Founder</p>
    <ul class="contact__list">
      <li class="contact__item">
        <svg class="contact__icon" viewBox="0 0 16 16" aria-hidden="true"><path d="M3.5 1 L6 1 L7 5 L5.2 6.3 C6 8 7.8 9.9 9.7 10.8 L11 9 L15 10 L15 12.5 C15 14 13.8 15 12.3 15 C6.3 14.5 1.5 9.7 1 3.7 C1 2.2 2 1 3.5 1 Z" fill="var(--accent-red)"/></svg>
        555 014 2538
      </li>
      <li class="contact__item">
        <svg class="contact__icon" viewBox="0 0 16 16" aria-hidden="true"><rect x="1" y="3" width="14" height="10" fill="var(--accent-red)"/><path d="M1 3 L8 9 L15 3" fill="none" stroke="#fff" stroke-width="1.4"/></svg>
        hello@bayline.test
      </li>
      <li class="contact__item">
        <svg class="contact__icon" viewBox="0 0 16 16" aria-hidden="true"><circle cx="8" cy="8" r="7" fill="var(--accent-red)"/><path d="M5 4 C7 5 6 7 8 8 C9 9 7 11 9 13 M10 3 C11 5 13 5 14 7" fill="none" stroke="#fff" stroke-width="1.2"/></svg>
        www.bayline.test
      </li>
    </ul>
  </div>

  <svg class="corner-swoosh corner-swoosh--bottom-right" viewBox="0 0 175 175" aria-hidden="true">
    <path d="M0 0 H162 C85 12 18 75 0 162 Z" fill="var(--accent-red)"/>
    <path d="M160 2 C80 18 16 82 3 165" fill="none" stroke="var(--ink-black)" stroke-width="5" stroke-linecap="round"/>
  </svg>
</section>

<section class="card card--back" aria-label="Business card back">
  <div class="note-lines" aria-label="Lines for handwritten notes">
    <span class="note-lines__rule" style="top:55px"></span>
    <span class="note-lines__rule" style="top:108px"></span>
    <span class="note-lines__rule" style="top:157px"></span>
    <span class="note-lines__rule" style="top:205px"></span>
    <span class="note-lines__rule" style="top:262px"></span>
  </div>

  <div class="brand-name"><span class="brand-name__dot"></span>Bayline Mosquito</div>
</section>

</body>
</html>
```